Business Card Design - ChoiceCraft

Looking for creative, modern design, two sided for ChoiceCraft that is consistent with color and feel of website www.choicecraftpro.net.
Updates

Back of card will be used to promote products or have a quote revolving around decisions, change, leadership, innovation, creativity. Back should also have space to promote website, but optional to use the icon. Front of the card will need to use the icon and have standard place for name, job title, phone and email. We are not looking to put a mailing address or fax. Also want space to place a few words/phrase explaining what we do...such as individual growth and organizational development or tools, training, information...in addition, want the facebook icon small on the front somewhere as we are also on facebook.

Vector file uploaded of icon.

Target Market(s)

Professional coaching for individual growth and organizational development

Industry/Entity Type

Business

Requirements
Must have
• Icon...see attached.

```html
<!DOCTYPE html>
<html lang="en">
<head>
<meta charset="utf-8">
<title>ChoiceCraft Business Card</title>
<link rel="stylesheet" href="https://fonts.googleapis.com/css2?family=PT+Sans:wght@400;700&family=Arimo:wght@400;700&display=swap">
<style>
  :root {
    --page-bg: #e4e6e8;
    --card-bg: #ffffff;
    --card-edge: #8a8d90;
    --ink-dark: #1f1f1f;
    --ink-mid: #555555;
    --ink-soft: #6b6b6b;
    --accent-blue: #2a9fd6;
    --logo-blue: #3d8fd4;
    --head-light: #eef4fb;
    --head-mid: #bcd2ea;
    --head-edge: #8f97c4;
    --quote-grey: #777777;
  }
  * { margin: 0; padding: 0; box-sizing: border-box; }
  html, body {
    width: 1200px;
    height: 1040px;
    overflow: hidden;
    background: var(--page-bg);
  }
  .canvas {
    position: relative;
    width: 1200px;
    height: 1040px;
  }
  .card {
    position: absolute;
    background: var(--card-bg);
    border: 1.5px solid var(--card-edge);
    border-radius: 36px;
    overflow: hidden;
  }
  /* Front */
  .card-front {
    left: 65px; top: 55px; width: 779px; height: 442px;
    font-family: "PT Sans", sans-serif;
  }
  .head-illustration {
    position: absolute;
    left: 16px; top: 14px;
    width: 310px; height: 385px;
    border-radius: 48% 52% 30% 40% / 42% 46% 30% 30%;
    background: linear-gradient(180deg, var(--head-light) 0%, var(--head-mid) 55%, var(--head-light) 100%);
    border: 3px solid var(--head-edge);
    border-bottom: none;
  }
  .brand-mark {
    position: absolute;
    left: 580px; top: 14px;
    width: 134px; height: 134px;
    border-radius: 50%;
    background: var(--logo-blue);
  }
  .front-details {
    position: absolute;
    right: 34px; top: 198px;
    text-align: right;
  }
  .brand-name {
    font-size: 27px;
    font-weight: 700;
    color: var(--ink-dark);
    letter-spacing: 0.3px;
    line-height: 34px;
  }
  .person {
    font-size: 28px;
    font-weight: 700;
    color: var(--ink-mid);
    line-height: 42px;
  }
  .person .title {
    font-weight: 400;
    font-size: 24px;
  }
  .contact-list {
    list-style: none;
    margin-top: 6px;
  }
  .contact-list li {
    font-size: 19px;
    color: var(--ink-mid);
    line-height: 26.5px;
    display: flex;
    justify-content: flex-end;
    align-items: center;
    gap: 8px;
  }
  .contact-list svg { width: 14px; height: 14px; }
  .social-square {
    width: 13px; height: 13px;
    background: var(--ink-soft);
    display: inline-block;
  }
  .tagline {
    position: absolute;
    right: 34px; top: 400px;
    font-size: 20.5px;
    color: var(--ink-mid);
    white-space: nowrap;
  }
  /* Back */
  .card-back {
    left: 363px; top: 540px; width: 771px; height: 439px;
    font-family: "Arimo", sans-serif;
  }
  .quote-list {
    list-style: none;
    position: absolute;
    left: 50px; top: 34px;
  }
  .quote {
    position: relative;
    padding-left: 26px;
    margin-bottom: 15px;
  }
  .quote-text {
    font-size: 20px;
    color: var(--ink-mid);
    line-height: 32px;
    white-space: nowrap;
  }
  .quote-text::before {
    content: "\201C";
    position: absolute;
    left: 0; top: -8px;
    font-size: 40px;
    font-weight: 700;
    color: var(--quote-grey);
  }
  .quote-text::after {
    content: "\201D";
    font-size: 40px;
    font-weight: 700;
    color: var(--quote-grey);
    position: relative;
    top: 16px;
    margin-left: 3px;
    line-height: 0;
  }
  .quote-author {
    font-size: 20px;
    font-weight: 700;
    color: var(--accent-blue);
    line-height: 28px;
  }
  .quote-author .dash { color: var(--ink-mid); font-weight: 400; }
  .back-brand {
    position: absolute;
    left: 540px; top: 252px;
    display: flex;
    flex-direction: column;
    align-items: center;
    gap: 8px;
  }
  .back-brand .brand-circle {
    width: 130px; height: 130px;
    border-radius: 50%;
    background: var(--logo-blue);
    opacity: 0.55;
  }
  .back-brand .brand-name {
    font-family: "PT Sans", sans-serif;
    font-size: 20px;
    color: var(--logo-blue);
    line-height: 22px;
  }
</style>
</head>
<body>
<main class="canvas">
  <section class="card card-front" aria-label="Card front">
    <div class="head-illustration" role="img" aria-label="Illustration of a head profile in soft blue with gears inside"></div>
    <div class="brand-mark" aria-hidden="true"></div>
    <div class="front-details">
      <div class="brand-name">ChoiceCraft</div>
      <div class="person">Your Name, <span class="title">Title</span></div>
      <ul class="contact-list">
        <li>
          <svg viewBox="0 0 16 16" aria-hidden="true"><circle cx="8" cy="8" r="7" fill="none" stroke="#555" stroke-width="1.4"/><path d="M5 4.5c.6-.4 1.2-.3 1.5.3l.6 1.2-.9.8c.4 1 1 1.7 2 2.1l.8-.9 1.2.6c.6.3.7.9.3 1.5-.6.8-1.6.9-2.6.3C6.4 9.5 5.4 8.3 4.8 6.9c-.3-1 -.3-1.9.2-2.4z" fill="#555"/></svg>
          123-456-789
        </li>
        <li>
          <svg viewBox="0 0 16 16" aria-hidden="true"><rect x="2" y="4" width="12" height="9" rx="1" fill="#555"/><path d="M2.5 4.5 8 9l5.5-4.5" fill="none" stroke="#fff" stroke-width="1.2"/></svg>
          info@choicecraftpro.net
        </li>
        <li>
          <svg viewBox="0 0 16 16" aria-hidden="true"><circle cx="8" cy="8" r="6.5" fill="none" stroke="#555" stroke-width="1.4"/><ellipse cx="8" cy="8" rx="2.8" ry="6.5" fill="none" stroke="#555" stroke-width="1.1"/><path d="M1.5 8h13" stroke="#555" stroke-width="1.1"/></svg>
          www.choicecraftpro.net
        </li>
        <li>
          <span class="social-square" aria-hidden="true"></span>
          /choicecraftpro
        </li>
      </ul>
    </div>
    <p class="tagline">Supporting individual growth and organizational development.</p>
  </section>

  <section class="card card-back" aria-label="Card back">
    <ul class="quote-list">
      <li class="quote">
        <p class="quote-text">Try not to become a man of success, but rather a man of value.</p>
        <p class="quote-author"><span class="dash">- </span>Alden Everett</p>
      </li>
      <li class="quote">
        <p class="quote-text">The only constant is change.</p>
        <p class="quote-author"><span class="dash">- </span>Theron Halis</p>
      </li>
      <li class="quote">
        <p class="quote-text">We are what we repeatedly do. Excellence is not an act, it is a habit.</p>
        <p class="quote-author"><span class="dash">- </span>Aristo Melane</p>
      </li>
      <li class="quote">
        <p class="quote-text">Simplicity is the ultimate sophistication.</p>
        <p class="quote-author"><span class="dash">- </span>Lorenzo Davelli</p>
      </li>
      <li class="quote">
        <p class="quote-text">Life is not fair - get used to it.</p>
        <p class="quote-author"><span class="dash">- </span>Bram Gaitley</p>
      </li>
    </ul>
    <div class="back-brand">
      <div class="brand-circle" aria-hidden="true"></div>
      <div class="brand-name">ChoiceCraft</div>
    </div>
  </section>
</main>
</body>
</html>
```